Satchel & Sundial needs new business card design

I need a new business card design. I'm looking for out-of-the-box design which represents the freedom of being a location independent entrepreneur.
I offer coaching, retreats and trips.
I would like to see designs with and without the photo.
Colors I use are black (#000000), green (#25A796) and brown (#D7C38C)
Website satchelandsundial.example

Target Market(s)

location independent entrepreneurs, digital nomads, people looking to swap the 9 to 5 for a lifestyle business

Industry/Entity Type

Business

Contact Information for Business Card

Dorota Falkner
Your Lifestyle Business Coach, Retreat & Trip Leader
http://satchelandsundial.example
hello@satchelandsundial.example
Live a life you don't need a holiday from

Font styles to use
Serif
Sans Serif

Requirements
Must have
• One side should contain only the logo. I would also consider having the "Live a life you don't need a holiday from" on that side too (depending on how it looks)
• Please show both sides on the designs.

```html
<!DOCTYPE html>
<html lang="en">
<head>
<meta charset="utf-8">
<title>Satchel &amp; Sundial — Business Card</title>
<link rel="stylesheet" href="https://fonts.googleapis.com/css2?family=Arimo:wght@400;700&display=swap">
<style>
  :root {
    --backdrop: #3b3b3d;
    --teal: #25a796;
    --teal-dark: #1d8b7d;
    --teal-light: #35b8a6;
    --ink: #2a2a2a;
    --grey-text: #4a4a4a;
    --paper: #ffffff;
    --paper-shade: #eeeeee;
  }
  * { box-sizing: border-box; margin: 0; padding: 0; }
  html, body {
    width: 1200px;
    height: 843px;
    overflow: hidden;
    background: var(--backdrop);
    font-family: "Arimo", Arial, sans-serif;
  }
  .canvas {
    position: relative;
    width: 1200px;
    height: 843px;
  }
  .card {
    position: absolute;
    left: 290px;
    width: 620px;
    height: 354px;
    box-shadow: 0 10px 28px rgba(0,0,0,0.45);
  }

  /* Logo side */
  .card--back {
    top: 44px;
    background: linear-gradient(160deg, var(--teal-light) 0%, var(--teal) 50%, var(--teal-dark) 100%);
    color: var(--paper);
  }
  .card--back .brand-name {
    position: absolute;
    left: 0; right: 0;
    top: 140px;
    text-align: center;
    font-size: 44px;
    font-weight: 700;
    letter-spacing: 2px;
    text-transform: uppercase;
    color: var(--paper);
  }
  .card--back .rule {
    position: absolute;
    left: 150px; right: 150px;
    bottom: 62px;
    height: 1px;
    background: rgba(255,255,255,0.45);
  }
  .card--back .tagline {
    position: absolute;
    left: 0; right: 0;
    bottom: 34px;
    text-align: center;
    font-size: 15px;
    letter-spacing: 0.5px;
    color: var(--paper);
  }

  /* Contact side */
  .card--front {
    top: 444px;
    background: linear-gradient(120deg, var(--paper) 0%, var(--paper) 60%, var(--paper-shade) 100%);
  }
  .person {
    position: absolute;
    left: 36px;
    top: 34px;
  }
  .person__name {
    font-size: 20px;
    font-weight: 700;
    color: var(--teal);
    text-transform: uppercase;
    letter-spacing: 0.5px;
    margin-bottom: 6px;
  }
  .person__role {
    font-size: 15px;
    line-height: 1.3;
    color: var(--grey-text);
  }
  .card--front .brand-name {
    position: absolute;
    right: 40px;
    top: 150px;
    font-size: 32px;
    font-weight: 700;
    letter-spacing: 1.5px;
    text-transform: uppercase;
    color: var(--ink);
  }
  .card--front .rule {
    position: absolute;
    left: 36px; right: 36px;
    top: 262px;
    height: 1px;
    background: var(--teal);
  }
  .contact {
    position: absolute;
    left: 36px; right: 36px;
    top: 280px;
    display: flex;
    gap: 22px;
    font-size: 14px;
    color: var(--grey-text);
    white-space: nowrap;
  }
  .contact__label {
    color: var(--teal);
    font-weight: 700;
  }
</style>
</head>
<body>
<main class="canvas">
  <section class="card card--back">
    <div class="brand-name">Satchel &amp; Sundial</div>
    <div class="rule"></div>
    <p class="tagline">Live a life you don't need a holiday from</p>
  </section>

  <section class="card card--front">
    <div class="person">
      <h1 class="person__name">Dorota Falkner</h1>
      <p class="person__role">Your Lifestyle Business Coach<br>Retreat &amp; Trip Leader</p>
    </div>
    <div class="brand-name">Satchel &amp; Sundial</div>
    <div class="rule"></div>
    <div class="contact">
      <span><span class="contact__label">Email :</span> hello@satchelandsundial.example</span>
      <span><span class="contact__label">Web :</span> www.satchelandsundial.example</span>
    </div>
  </section>
</main>
</body>
</html>
```